Northfield Builders Guild Business card

We are looking for a new business card design with photo included.
Our business is a nonprofit construction contractor membership organization. We offer business education, assist with business setup and licensing, provide safety training, and provide a member directory.
URL: www.builderslinkguild.org
Color code:
CMYK: 0 cyan, 42 magenta, 100 yellow, 0 black for Print.
Hexidecimal: #FF9900
RGB: R 255; G 153; B 0

```html
<!DOCTYPE html>
<html lang="en">
<head>
<meta charset="utf-8">
<title>Northfield Builders Guild – Business Card</title>
<link rel="stylesheet" href="https://fonts.googleapis.com/css2?family=Montserrat:wght@700;800&family=Arimo:wght@400&display=swap">
<style>
  :root {
    --orange: #ff9900;
    --ink: #0b0b0b;
    --band: #e1e1e1;
    --paper-bg: #2b2b2b;
    --white: #ffffff;
    --muted: #151515;
  }
  * { margin: 0; padding: 0; box-sizing: border-box; }
  html, body { width: 1200px; height: 1015px; overflow: hidden; }
  body {
    background: var(--paper-bg);
    display: flex; flex-direction: column; align-items: center; justify-content: center;
    gap: 50px;
    font-family: "Arimo", Arial, sans-serif;
  }
  .card {
    width: 760px; height: 434px; position: relative; overflow: hidden;
    box-shadow: 0 12px 30px rgba(0,0,0,.55);
  }

  /* Back */
  .card-back { background: var(--ink); }
  .back-texture {
    position: absolute; inset: 0;
    background: linear-gradient(135deg, #121212 0%, #0a0a0a 50%, #141414 100%);
  }
  .back-wordmark {
    position: absolute; left: 50%; top: 50%; transform: translate(-50%, -50%);
    font-family: "Montserrat", sans-serif; font-weight: 800;
    color: var(--white); font-size: 30px; line-height: 1.05;
    text-transform: uppercase; text-align: left; letter-spacing: .5px;
  }

  /* Front */
  .card-front { background: var(--ink); }
  .brand-band {
    position: absolute; left: 0; top: 0; width: 100%; height: 190px;
    background: var(--band);
    display: flex; align-items: flex-end; padding: 0 0 34px 70px;
  }
  .brand-name {
    font-family: "Montserrat", sans-serif; font-weight: 800;
    font-size: 44px; color: var(--ink); text-transform: uppercase;
    letter-spacing: -.5px; line-height: 1;
  }
  .person { position: absolute; left: 100px; top: 220px; }
  .person-name {
    font-family: "Montserrat", sans-serif; font-weight: 800;
    color: var(--orange); font-size: 30px; text-transform: uppercase; line-height: 1;
  }
  .person-title {
    font-family: "Montserrat", sans-serif; font-weight: 700;
    color: var(--band); font-size: 19px; text-transform: uppercase; margin-top: 6px;
  }
  .contacts { position: absolute; left: 120px; top: 310px; list-style: none; }
  .contacts li {
    display: flex; align-items: center; gap: 10px;
    color: var(--white); font-size: 19px; height: 26px;
  }
  .contacts svg { width: 22px; height: 22px; flex: none; }
  .address {
    position: absolute; left: 450px; top: 240px;
    color: var(--white); font-size: 19px; line-height: 1.25; font-style: normal;
  }
  .web { color: var(--orange); margin-top: 14px; display: block; }
</style>
</head>
<body>

<section class="card card-back" aria-label="Card back">
  <div class="back-texture" role="img" aria-label="Faint repeated diagonal wordmark pattern on black"></div>
  <div class="back-wordmark">Northfield<br>Builders Guild</div>
</section>

<section class="card card-front" aria-label="Card front">
  <div class="brand-band">
    <div class="brand-name">Northfield Builders Guild</div>
  </div>

  <div class="person">
    <div class="person-name">Daniel Reyes</div>
    <div class="person-title">Managing Director</div>
  </div>

  <ul class="contacts">
    <li>
      <svg viewBox="0 0 22 22" aria-hidden="true"><circle cx="11" cy="11" r="11" fill="var(--orange)"/><path d="M7.5 6c.6-.5 1.2-.4 1.5.1l1 1.6c.3.5.2 1-.2 1.3l-.7.5c.6 1.3 1.5 2.2 2.8 2.8l.5-.7c.3-.4.8-.5 1.3-.2l1.6 1c.5.3.6.9.1 1.5-.8 1-2 1.3-3.3.6-2.3-1.1-4-2.8-5.1-5.1-.6-1.3-.3-2.5.5-3.4z" fill="#fff"/></svg>
      (555) 014-2290
    </li>
    <li>
      <svg viewBox="0 0 22 22" aria-hidden="true"><circle cx="11" cy="11" r="11" fill="var(--orange)"/><rect x="7.5" y="5" width="7" height="12" rx="1.3" fill="none" stroke="#fff" stroke-width="1.5"/><circle cx="11" cy="14.8" r=".8" fill="#fff"/></svg>
      800-555-0176
    </li>
    <li>
      <svg viewBox="0 0 22 22" aria-hidden="true"><circle cx="11" cy="11" r="11" fill="var(--orange)"/><rect x="8" y="5.5" width="6" height="3.5" fill="#fff"/><rect x="5.5" y="9" width="11" height="5" rx="1" fill="#fff"/><rect x="8" y="12.5" width="6" height="4" fill="#fff" stroke="var(--orange)" stroke-width=".8"/></svg>
      555.010.0843
    </li>
    <li>
      <svg viewBox="0 0 22 22" aria-hidden="true"><circle cx="11" cy="11" r="11" fill="var(--orange)"/><rect x="5.5" y="7" width="11" height="8" fill="#fff"/><path d="M5.5 7l5.5 4.5L16.5 7" fill="none" stroke="var(--orange)" stroke-width="1.2"/></svg>
      support@nfbguild.org
    </li>
  </ul>

  <address class="address">
    2400 Hartwell Ave<br>
    Suite #210, Northfield<br>
    MN 55057
    <span class="web">www.builderslinkguild.org</span>
  </address>
</section>

</body>
</html>
```